Luxury Wine Label for New Startup Winery

We need a wine label for our new winery startup. We have worked with a local designer but do not feel the resulting label / logo have the elevation required to present our brand as a luxury wine. Our winery is called "Quailbrook Vineyards" and we are focused on extremely high quality hand crafted artisan and estate wines from the Pacific Northwest.
We would like to see designs that utilize a tree line, or other imagery that represents the "Quailbrook" part of our company name. Another interesting feature could be wood grain.
A logo will be required based on your design so please design with this in mind:
This logo should be consistent with the wine bottle label design, and should be representative of our high end exclusive wine while giving a sense of place (Oregon/ Pacific Northwest.)
I will supply an image of the design we received from our local designer, PLEASE NOTE: in general we do like wood grain and tree line concepts but feel the execution was poorly done.
ATTN: Logo design should be suitable for use on: Bottles (Red wine/rose/white wine), Bussiness cards, vehicle signage, business signage, etc
P.S.:
If you have a design that is not outside the box we are still interested in seeing it.
Label is for a burgundy style bottle with a label height of 3.5 - 4" and a width of 3.5-4"
any label <= 4"x4" and >=3.5"x3.5" will be acceptable:
HOWEVER Width should be greater than or equal to height due to the bottle format
Target Market(s)
Wine enthusiasts with adequate discretionary budgets to afford $100 bottles of wine.
Industry/Entity Type
Wine / Winery
Requirements
Must have
- A sense of luxury, a feel of exclusivity, and a theme consistent with our product and brand name
Nice to have
- Tree line, wood grain or other wood themes. Serif fonts
Should not have
- anything cheesy, off topic, hard to read script fonts or anything that makes the label hard to read from a few feet away or too busy

```html
<!DOCTYPE html>
<html lang="en">
<head>
<meta charset="UTF-8">
<title>Quailbrook Vineyards — Syrah Label</title>
<link rel="stylesheet" href="https://fonts.googleapis.com/css2?family=Cinzel:wght@400;500&family=Roboto+Slab:wght@400;700&display=swap">
<style>
  :root {
    --paper: #ffffff;
    --label-black: #1b1b1b;
    --silver-dark: #6f6f6f;
    --silver-mid: #bdbdbd;
    --silver-light: #f4f4f4;
    --gold-dark: #c9a443;
    --gold-light: #f6e27a;
    --gold-text: #ecd66c;
    --wordmark: #cfcfcf;
    --wood-dark: #3e2a1c;
    --wood-mid: #6b4a34;
    --ink: #1e1a12;
  }
  * { box-sizing: border-box; margin: 0; padding: 0; }
  html, body {
    width: 1130px;
    height: 1200px;
    overflow: hidden;
    background: var(--paper);
  }
  .canvas {
    position: relative;
    width: 1130px;
    height: 1200px;
  }

  /* Front label */
  .front-label {
    position: absolute;
    left: 16px;
    top: 16px;
    width: 1098px;
    height: 891px;
    background: var(--label-black);
  }
  .silver-band {
    position: absolute;
    left: 0;
    width: 100%;
    background: linear-gradient(90deg, var(--silver-dark) 0%, var(--silver-mid) 20%, var(--silver-light) 50%, var(--silver-mid) 80%, var(--silver-dark) 100%);
  }
  .silver-band--top { top: 0; height: 32px; }
  .silver-band--bottom { bottom: 0; height: 35px; }
  .gold-stripe {
    position: absolute;
    left: 0;
    width: 100%;
    height: 9px;
    background: linear-gradient(90deg, var(--gold-dark), var(--gold-light) 50%, var(--gold-dark));
  }
  .gold-stripe--upper { top: 812px; }
  .gold-stripe--lower { top: 834px; }

  .brand-mark {
    position: absolute;
    left: 50%;
    top: 190px;
    width: 170px;
    height: 170px;
    margin-left: -85px;
    border-radius: 50%;
    background: var(--gold-dark);
  }
  .brand-name {
    position: absolute;
    left: 0;
    width: 100%;
    text-align: center;
    font-family: "Cinzel", serif;
    font-weight: 400;
    color: var(--wordmark);
    line-height: 1;
  }
  .brand-name--primary {
    top: 440px;
    font-size: 92px;
    letter-spacing: 2px;
  }
  .brand-name--secondary {
    top: 560px;
    font-size: 66px;
    letter-spacing: 8px;
  }
  .appellation {
    position: absolute;
    left: 0;
    top: 712px;
    width: 100%;
    text-align: center;
    font-family: "Roboto Slab", serif;
    font-weight: 400;
    font-size: 38px;
    letter-spacing: 5px;
    color: var(--gold-text);
  }

  .notch {
    position: absolute;
    left: 835px;
    top: 925px;
  }

  /* Varietal strip */
  .varietal-label {
    position: absolute;
    left: 16px;
    top: 941px;
    width: 1098px;
    height: 245px;
  }
  .gold-band {
    position: absolute;
    left: 0;
    width: 100%;
    background: linear-gradient(90deg, var(--gold-dark), var(--gold-light) 50%, var(--gold-dark));
  }
  .gold-band--top { top: 0; height: 36px; }
  .gold-band--bottom {
    bottom: 0;
    height: 37px;
    display: flex;
    align-items: center;
    justify-content: center;
  }
  .wood-panel {
    position: absolute;
    left: 0;
    top: 36px;
    width: 100%;
    height: 172px;
    background: linear-gradient(180deg, var(--wood-mid) 0%, var(--wood-dark) 45%, var(--wood-mid) 70%, var(--wood-dark) 100%);
  }
  .varietal {
    position: absolute;
    left: 0;
    top: 76px;
    width: 100%;
    text-align: center;
    font-family: "Cinzel", serif;
    font-weight: 400;
    font-size: 90px;
    letter-spacing: 22px;
    padding-left: 22px;
    color: var(--silver-light);
    line-height: 1;
  }
  .vintage-line {
    font-family: "Roboto Slab", serif;
    font-weight: 700;
    font-size: 20px;
    letter-spacing: 3px;
    color: var(--ink);
  }
</style>
</head>
<body>
<main class="canvas">

  <section class="front-label">
    <div class="silver-band silver-band--top"></div>

    <div class="brand-mark" aria-hidden="true"></div>
    <h1 class="brand-name brand-name--primary">QUAILBROOK</h1>
    <p class="brand-name brand-name--secondary">VINEYARDS</p>

    <p class="appellation">“WILLAMETTE VALLEY”</p>

    <div class="gold-stripe gold-stripe--upper"></div>
    <div class="gold-stripe gold-stripe--lower"></div>
    <div class="silver-band silver-band--bottom"></div>
  </section>

  <svg class="notch" width="18" height="14" viewBox="0 0 18 14" aria-hidden="true">
    <polygon points="9,0 18,14 0,14" fill="#111111"/>
  </svg>

  <section class="varietal-label">
    <div class="gold-band gold-band--top"></div>
    <div class="wood-panel" role="img" aria-label="Dark walnut wood grain texture"></div>
    <h2 class="varietal">SYRAH</h2>
    <div class="gold-band gold-band--bottom">
      <p class="vintage-line">ESTATE | 2023 | GROWN</p>
    </div>
  </section>

</main>
</body>
</html>
```